Bright Towns Forum PowerPoint Design Template and Sample Deck

The Bright Towns Forum is an international organization that seeks to improve the livability, workability and sustainability of the world’s cities.
We seek a versatile PowerPoint design template with 10 slide types plus a “self-documenting” sample deck. Your design will be used in keynote speeches and workshops around the world.
After the contest is completed, we will ask the winning designer to add 10-20 additional slide types for $75 per slide. We also seek a long-term relationship whereby we can request “custom” slides and/or ask the designer to touch up the slides we build to make them better.
FILES. We have uploaded several files:
2. PALETTE. Shows our official colors.
3 LOGOS. Several individual files with different variations of our logo. Some with our motto, some without.
2. SAMPLE SLIDES. Because we were unable to successfully upload our sample deck, we are making it available via this FileNook link:
https://www.filenook-example.com/s/k7qrtmzp2wd9hxa/The%20Bright%20Towns%20Forum%20Design%20Contest%20Notes.docx?dl=0
Target Market(s)
Mayors, department heads, CIOs, senior executives from technology companies
Industry/Entity Type
Information Technology
Colors
Designer to choose colors to be used in the design.
Requirements
Must have
- Please see uploaded Word document for requirements, nice to haves and should not haves and uploaded palette for color preferences.
Nice to have
- see above
Should not have
- see above

```html
<!DOCTYPE html>
<html lang="en">
<head>
<meta charset="utf-8">
<title>Bright Towns Forum – Slide Template Deck</title>
<link rel="stylesheet" href="https://fonts.googleapis.com/css2?family=Open+Sans:wght@400;600;700;800&display=swap">
<style>
:root{
  --navy:#173a6b;
  --navy-dark:#10284d;
  --orange:#f29a1f;
  --green:#6aa43b;
  --purple:#7b3f98;
  --red:#e8502a;
  --teal:#1a9bc2;
  --grey:#e6e8ec;
  --grey-mid:#b8bec8;
  --ink:#2b2f36;
  --white:#ffffff;
}
*{box-sizing:border-box;margin:0;padding:0}
html,body{width:1200px;height:3331px;overflow:hidden;background:#f3f4f6}
body{font-family:"Open Sans",Arial,sans-serif;color:var(--ink)}
.deck{display:grid;grid-template-columns:repeat(3,384px);grid-auto-rows:212px;gap:10px 11px;padding:6px 13px 5px}
.slide{position:relative;overflow:hidden;background:var(--white);box-shadow:0 1px 3px rgba(0,0,0,.25)}
.slide > *{position:absolute}
.last{grid-column:2}
.ph{display:block}
.ph-dusk{background:linear-gradient(180deg,#3d4a63 0%,#7f6a5e 55%,#2a2f3d 100%)}
.ph-day{background:linear-gradient(180deg,#a9bcd1 0%,#5d7591 60%,#2f3e52 100%)}
.ph-night{background:linear-gradient(135deg,#1c2533 0%,#4a4f5c 55%,#8a6b4a 100%)}
.ph-aerial{background:linear-gradient(135deg,#2e3a44 0%,#6b7480 50%,#3c4650 100%)}
.ph-sunset{background:linear-gradient(180deg,#5d7aa0 0%,#c79a72 60%,#3a4256 100%)}
.navy{background:var(--navy)}
.orange{background:var(--orange)}
.logo{font-weight:700;color:var(--navy);line-height:1.1;white-space:nowrap}
.logo.inv{color:var(--white)}
.hd{left:10px;top:7px;font-size:12px;font-weight:700;color:var(--navy)}
.ft{left:0;right:0;bottom:0;height:11px;border-top:2px solid var(--navy);font-size:5px;display:flex;justify-content:space-between;align-items:center;padding:0 8px;color:#555}
.ft b{color:var(--navy)}
.wt{color:var(--white)}
.tiny{font-size:5.5px;line-height:1.35;color:#555}
.tiny.wt{color:#e8ecf3}
.h-sm{font-size:7px;font-weight:700}
.big-title{font-weight:700;line-height:1.15}
.bar{border-radius:1px}
table.grid{border-collapse:collapse;font-size:4.5px;color:#444}
table.grid th{background:var(--navy);color:#fff;padding:3px 2px;font-weight:600}
table.grid td{padding:2.5px 2px;border-bottom:1px solid #dde;text-align:center}
table.grid td:first-child{background:var(--navy-dark);color:#fff}
.agenda li{list-style:none;font-size:9px;color:var(--navy);line-height:15px;padding-left:6px}
.agenda li.on{color:var(--orange)}
.agenda.fill li.on{background:#fbd9a8;color:var(--navy)}
.stat{font-size:20px;font-weight:700;text-align:center}
.dot{border-radius:50%}
</style>
</head>
<body>
<main class="deck">

<section class="slide">
  <div class="ph ph-dusk" style="left:0;top:0;right:0;height:140px" role="img" aria-label="City skyline at dusk"></div>
  <h1 class="big-title wt" style="left:0;right:0;top:52px;text-align:center;font-size:19px">Your Title Goes Here</h1>
  <p class="wt" style="left:0;right:0;top:78px;text-align:center;font-size:6px">Your Subtitle Goes Here</p>
  <div class="logo" style="left:22px;top:162px;font-size:15px">Bright Towns Forum</div>
  <div style="right:20px;top:168px;font-size:6px;color:var(--navy)">www.brighttownsforum.org</div>
</section>

<section class="slide">
  <div class="logo" style="right:18px;top:8px;font-size:10px">Bright Towns Forum</div>
  <div class="ph ph-sunset" style="left:0;top:28px;right:0;height:130px" role="img" aria-label="Skyline across the water at sunset"></div>
  <div class="navy" style="left:70px;top:70px;width:130px;height:95px"></div>
  <h1 class="big-title wt" style="left:84px;top:88px;width:110px;font-size:16px">Your Title Goes Here</h1>
  <p class="wt" style="left:84px;top:130px;font-size:5.5px">Your Subtitle Goes Here</p>
  <div style="right:20px;top:180px;font-size:6px;color:var(--navy)">www.brighttownsforum.org</div>
</section>

<section class="slide">
  <div class="navy" style="left:0;top:0;right:0;height:120px"></div>
  <div class="logo inv" style="left:0;right:0;top:44px;text-align:center;font-size:17px">Bright Towns Forum</div>
  <p class="wt" style="left:0;right:0;top:70px;text-align:center;font-size:7px">Better places to live and work</p>
  <h1 class="big-title" style="left:0;right:0;top:150px;text-align:center;color:var(--navy);font-size:17px">Your Title Goes Here</h1>
  <p style="left:0;right:0;top:176px;text-align:center;font-size:6px;color:var(--navy)">Your Subtitle Goes Here</p>
</section>

<section class="slide">
  <div class="navy" style="left:0;right:0;top:90px;bottom:0"></div>
  <div class="ph ph-day" style="left:0;top:0;width:200px;height:140px" role="img" aria-label="Aerial view of downtown towers"></div>
  <div class="navy" style="left:24px;top:36px;width:132px;height:34px"></div>
  <div class="logo inv" style="left:34px;top:46px;font-size:12px">Bright Towns Forum</div>
  <h1 class="big-title wt" style="right:20px;top:150px;font-size:17px">Your Title Goes Here</h1>
  <p class="wt" style="right:20px;top:176px;font-size:6px">Your Subtitle Goes Here</p>
</section>

<section class="slide">
  <div class="navy" style="left:0;top:80px;width:220px;height:56px"></div>
  <h1 class="big-title wt" style="left:16px;top:90px;font-size:16px">Your Title Goes Here</h1>
  <p class="wt" style="left:60px;top:116px;font-size:5.5px">Your Subtitle Goes Here</p>
  <div class="logo" style="left:236px;top:100px;font-size:12px">Bright Towns Forum</div>
</section>

<section class="slide">
  <div class="navy" style="left:0;top:0;width:205px;bottom:0"></div>
  <h2 class="big-title wt" style="left:14px;top:85px;font-size:13px">Progressive Agenda</h2>
  <div class="logo inv" style="left:14px;top:104px;font-size:9px">Bright Towns Forum</div>
  <ul class="agenda" style="left:220px;top:48px">
    <li>Our Agenda 1</li><li>Our Agenda 2</li><li class="on">Our Agenda 3</li><li>Our Agenda 4</li><li>Our Agenda 5</li><li>Our Agenda 6</li>
  </ul>
</section>

<section class="slide">
  <h2 class="big-title" style="left:34px;top:92px;font-size:13px;color:var(--navy)">Progressive Agenda</h2>
  <div class="logo" style="left:34px;top:110px;font-size:9px">Bright Towns Forum</div>
  <div style="left:198px;top:48px;width:1px;height:120px;background:var(--grey-mid)"></div>
  <ul class="agenda fill" style="left:204px;top:50px;width:130px">
    <li>Our Agenda 1</li><li>Our Agenda 2</li><li class="on">Our Agenda 3</li><li>Our Agenda 4</li><li>Our Agenda 5</li><li>Our Agenda 6</li>
  </ul>
</section>

<section class="slide">
  <div class="ph ph-night" style="inset:0" role="img" aria-label="Aerial night view of a highway interchange"></div>
  <div class="navy" style="left:0;top:0;width:150px;bottom:0;opacity:.92"></div>
  <h2 class="big-title wt" style="left:16px;top:86px;width:125px;font-size:13px">Full Bleed Picture With 1 Banners</h2>
</section>

<section class="slide">
  <div class="ph ph-aerial" style="left:0;top:0;right:0;height:125px" role="img" aria-label="Aerial view of city blocks"></div>
  <h2 class="big-title wt" style="left:12px;top:30px;font-size:13px">Full Bleed Picture Banners</h2>
  <div class="navy" style="left:0;right:0;top:125px;bottom:0"></div>
  <p class="h-sm wt" style="left:12px;top:136px">Heading Here</p>
  <p class="tiny wt" style="left:12px;top:148px;width:360px">Lorem ipsum dolor sit amet, consectetur adipiscing elit, sed do eiusmod tempor incididunt ut labore et dolore magna aliqua. Ut enim ad minim veniam, quis nostrud exercitation ullamco laboris nisi ut aliquip ex ea commodo consequat duis aute irure.</p>
</section>

<section class="slide">
  <div class="ph ph-aerial" style="inset:0" role="img" aria-label="Aerial view of towers and streets"></div>
  <div class="navy" style="left:0;top:0;width:128px;height:100px;opacity:.92"></div>
  <div class="orange" style="left:128px;top:0;width:128px;height:100px"></div>
  <div class="navy" style="left:256px;top:0;width:128px;height:100px;opacity:.92"></div>
  <p class="h-sm wt" style="left:8px;top:8px">Heading Here</p>
  <p class="tiny wt" style="left:8px;top:20px;width:112px">Lorem ipsum dolor sit amet, consectetur adipiscing elit sed do eiusmod tempor.</p>
  <p class="h-sm wt" style="left:136px;top:8px">Heading Here</p>
  <p class="tiny wt" style="left:136px;top:20px;width:112px">Lorem ipsum dolor sit amet, consectetur adipiscing elit sed do eiusmod tempor.</p>
  <p class="h-sm wt" style="left:264px;top:8px">Heading Here</p>
  <p class="tiny wt" style="left:264px;top:20px;width:112px">Lorem ipsum dolor sit amet, consectetur adipiscing elit sed do eiusmod tempor.</p>
  <h2 class="big-title wt" style="left:12px;top:170px;font-size:13px">Full Bleed Picture Banners</h2>
</section>

<section class="slide">
  <div class="navy" style="left:0;top:0;width:125px;bottom:0"></div>
  <h2 class="big-title wt" style="left:14px;top:80px;width:105px;font-size:12px">Full Bleed Picture With Banners</h2>
  <div class="ph ph-aerial" style="left:125px;top:0;right:0;bottom:0" role="img" aria-label="Aerial view of city blocks"></div>
  <div class="navy" style="left:150px;top:12px;width:220px;height:68px;opacity:.92"></div>
  <p class="h-sm wt" style="left:158px;top:18px">Heading Here</p>
  <p class="tiny wt" style="left:158px;top:30px;width:205px">Lorem ipsum dolor sit amet, consectetur adipiscing elit, sed do eiusmod tempor incididunt ut labore et dolore magna aliqua.</p>
  <div class="orange" style="left:125px;top:125px;right:0;bottom:0"></div>
  <p class="h-sm wt" style="left:158px;top:133px">Heading Here</p>
  <p class="tiny wt" style="left:158px;top:145px;width:205px">Lorem ipsum dolor sit amet, consectetur adipiscing elit, sed do eiusmod tempor incididunt ut labore et dolore magna aliqua.</p>
</section>

<section class="slide">
  <div class="navy" style="left:0;top:0;width:125px;bottom:0"></div>
  <h2 class="big-title wt" style="left:14px;top:80px;width:105px;font-size:12px">Full Bleed Picture With 3 Banners</h2>
  <div class="ph ph-sunset" style="left:125px;top:0;right:0;bottom:0" role="img" aria-label="Downtown skyline at golden hour"></div>
  <div class="navy" style="left:150px;top:20px;width:110px;height:165px;opacity:.92"></div>
  <p class="h-sm wt" style="left:158px;top:28px">Heading Here</p>
  <p class="tiny wt" style="left:158px;top:40px;width:95px">Lorem ipsum dolor sit amet, consectetur adipiscing elit, sed do eiusmod tempor incididunt ut labore et dolore magna aliqua ut enim ad minim veniam.</p>
</section>

<section class="slide">
  <h2 class="hd">Quotation Area #1</h2>
  <div class="ph ph-dusk" style="left:180px;top:40px;right:0;height:130px" role="img" aria-label="City waterfront at dusk"></div>
  <p style="left:16px;top:80px;width:160px;font-size:8.5px;font-style:italic;color:var(--navy);line-height:1.35">“Coming together is a beginning. Keeping together is progress. Working together is success.”</p>
  <p class="tiny" style="left:16px;top:122px">– Author Name</p>
  <div class="ft"><b>Bright Towns Forum</b><span>Sample footer · Page 1</span></div>
</section>

<section class="slide">
  <div class="ph ph-night" style="inset:0" role="img" aria-label="Dim city skyline"></div>
  <div class="navy" style="inset:0;opacity:.85"></div>
  <div class="orange dot" style="left:177px;top:36px;width:30px;height:30px"></div>
  <div class="wt" style="left:185px;top:34px;font-size:22px;font-weight:800">“</div>
  <p class="wt" style="left:0;right:0;top:82px;text-align:center;font-size:9px;line-height:1.4">Coming together is a beginning.<br>Keeping together is a progress.<br>Working together is success.</p>
  <p class="tiny wt" style="left:210px;top:134px">– Author Name</p>
</section>

<section class="slide">
  <h2 class="hd">Text Heavy With Complementary Picture</h2>
  <div class="ph ph-aerial" style="left:10px;top:30px;width:140px;height:120px" role="img" aria-label="Aerial view of a road junction"></div>
  <p class="tiny" style="left:160px;top:30px;width:214px;color:var(--orange)">Lorem ipsum dolor sit amet, consectetur adipiscing elit, sed do eiusmod tempor incididunt ut labore et dolore.</p>
  <p class="tiny" style="left:160px;top:56px;width:214px">Ut enim ad minim veniam, quis nostrud exercitation ullamco laboris nisi ut aliquip ex ea commodo consequat. Duis aute irure dolor in reprehenderit in voluptate velit esse cillum dolore eu fugiat nulla pariatur excepteur sint occaecat cupidatat non proident sunt in culpa qui officia.</p>
  <div class="ft"><b>Bright Towns Forum</b><span>Sample footer · Page 3</span></div>
</section>

<section class="slide">
  <h2 class="hd">Statistics Heavy</h2>
  <div class="stat" style="left:20px;top:62px;color:var(--green)">125</div>
  <div class="stat" style="left:110px;top:62px;color:var(--red)">26</div>
  <div class="stat" style="left:190px;top:62px;color:var(--purple)">252</div>
  <div class="stat" style="left:290px;top:62px;color:var(--orange)">56</div>
  <p class="tiny" style="left:20px;top:94px;width:80px">Headline Here. Short note on this figure.</p>
  <p class="tiny" style="left:105px;top:94px;width:80px">Headline Here. Short note on this figure.</p>
  <p class="tiny" style="left:190px;top:94px;width:80px">Headline Here. Short note on this figure.</p>
  <p class="tiny" style="left:280px;top:94px;width:80px">Headline Here. Short note on this figure.</p>
  <div class="ft"><b>Bright Towns Forum</b><span>Sample footer · Page 4</span></div>
</section>

<section class="slide">
  <div class="navy" style="left:0;top:0;right:0;height:22px"></div>
  <h2 class="hd wt" style="top:5px;color:#fff">Statistics Heavy</h2>
  <div class="dot" style="left:30px;top:55px;width:28px;height:28px;background:var(--green)"></div>
  <div class="dot" style="left:120px;top:55px;width:28px;height:28px;background:var(--red)"></div>
  <div class="dot" style="left:210px;top:55px;width:28px;height:28px;background:var(--purple)"></div>
  <div class="dot" style="left:300px;top:55px;width:28px;height:28px;background:var(--orange)"></div>
  <div class="wt" style="left:30px;top:62px;width:28px;text-align:center;font-size:9px;font-weight:700">25</div>
  <div class="wt" style="left:120px;top:62px;width:28px;text-align:center;font-size:9px;font-weight:700">26</div>
  <div class="wt" style="left:210px;top:62px;width:28px;text-align:center;font-size:9px;font-weight:700">52</div>
  <div class="wt" style="left:300px;top:62px;width:28px;text-align:center;font-size:9px;font-weight:700">56</div>
  <p class="tiny" style="left:14px;top:92px;width:70px">Headline Here. Short note on figure.</p>
  <p class="tiny" style="left:104px;top:92px;width:70px">Headline Here. Short note on figure.</p>
  <p class="tiny" style="left:194px;top:92px;width:70px">Headline Here. Short note on figure.</p>
  <p class="tiny" style="left:284px;top:92px;width:70px">Headline Here. Short note on figure.</p>
  <div class="ft"><b>Bright Towns Forum</b><span>Sample footer · Page 5</span></div>
</section>

<section class="slide">
  <h2 class="hd">World Map</h2>
  <div style="left:130px;top:28px;width:230px;height:110px;background:linear-gradient(90deg,#c9cdd4,#b6bcc5);border-radius:8px" role="img" aria-label="World map with highlighted regions"></div>
  <div class="orange" style="left:150px;top:45px;width:40px;height:28px"></div>
  <div class="navy" style="left:230px;top:55px;width:30px;height:25px"></div>
  <div style="left:320px;top:100px;width:26px;height:20px;background:var(--green)"></div>
  <div class="orange" style="left:20px;top:150px;width:10px;height:6px"></div>
  <div style="left:20px;top:162px;width:10px;height:6px;background:var(--green)"></div>
  <div class="navy" style="left:190px;top:150px;width:10px;height:6px"></div>
  <p class="tiny" style="left:34px;top:149px">Region label one</p>
  <p class="tiny" style="left:34px;top:161px">Region label two</p>
  <p class="tiny" style="left:204px;top:149px">Region label three</p>
  <div class="ft"><b>Bright Towns Forum</b><span>Sample footer · Page 6</span></div>
</section>

<section class="slide">
  <h2 class="hd">Two-column Table</h2>
  <table class="grid" style="left:10px;top:40px;width:175px">
    <tr><th colspan="5">Your Table Title Here</th></tr>
    <tr><td>A</td><td>10</td><td>20</td><td>30</td><td>40</td></tr>
    <tr><td>B</td><td>12</td><td>22</td><td>32</td><td>42</td></tr>
    <tr><td>C</td><td>14</td><td>24</td><td>34</td><td>44</td></tr>
    <tr><td>D</td><td>16</td><td>26</td><td>36</td><td>46</td></tr>
    <tr><td>E</td><td>18</td><td>28</td><td>38</td><td>48</td></tr>
  </table>
  <table class="grid" style="left:199px;top:40px;width:175px">
    <tr><th colspan="5">Your Table Title Here</th></tr>
    <tr><td>A</td><td>10</td><td>20</td><td>30</td><td>40</td></tr>
    <tr><td>B</td><td>12</td><td>22</td><td>32</td><td>42</td></tr>
    <tr><td>C</td><td>14</td><td>24</td><td>34</td><td>44</td></tr>
    <tr><td>D</td><td>16</td><td>26</td><td>36</td><td>46</td></tr>
    <tr><td>E</td><td>18</td><td>28</td><td>38</td><td>48</td></tr>
  </table>
  <div class="ft"><b>Bright Towns Forum</b><span>Sample footer · Page 7</span></div>
</section>

<section class="slide">
  <h2 class="hd">Two-column Table + Picture + Text</h2>
  <div style="left:10px;top:28px;width:170px;height:60px;background:var(--grey)"></div>
  <p class="tiny" style="left:16px;top:34px;width:158px">Lorem ipsum dolor sit amet, consectetur adipiscing elit, sed do eiusmod tempor incididunt ut labore.</p>
  <div class="ph ph-night" style="left:10px;top:95px;width:170px;height:90px" role="img" aria-label="City streets at night"></div>
  <table class="grid" style="left:192px;top:28px;width:182px">
    <tr><th colspan="5">Your Table Title</th></tr>
    <tr><td>A</td><td>10</td><td>20</td><td>30</td><td>40</td></tr>
    <tr><td>B</td><td>12</td><td>22</td><td>32</td><td>42</td></tr>
    <tr><td>C</td><td>14</td><td>24</td><td>34</td><td>44</td></tr>
  </table>
  <table class="grid" style="left:192px;top:110px;width:182px">
    <tr><th colspan="5">Your Table Title</th></tr>
    <tr><td>A</td><td>10</td><td>20</td><td>30</td><td>40</td></tr>
    <tr><td>B</td><td>12</td><td>22</td><td>32</td><td>42</td></tr>
    <tr><td>C</td><td>14</td><td>24</td><td>34</td><td>44</td></tr>
  </table>
  <div class="ft"><b>Bright Towns Forum</b><span>Sample footer · Page 8</span></div>
</section>

<section class="slide">
  <h2 class="hd">Two Pictures</h2>
  <div class="ph ph-day" style="left:10px;top:28px;width:178px;height:160px" role="img" aria-label="Midtown skyline by day"></div>
  <div class="ph ph-sunset" style="left:196px;top:28px;width:178px;height:160px" role="img" aria-label="Skyline at sunset"></div>
  <div class="navy" style="left:10px;top:28px;width:178px;height:14px"></div>
  <div class="navy" style="left:196px;top:28px;width:178px;height:14px"></div>
  <p class="h-sm wt" style="left:18px;top:31px;font-size:6px">Your Picture 1 Title</p>
  <p class="h-sm wt" style="left:204px;top:31px;font-size:6px">Your Picture 2 Title</p>
  <div class="orange" style="left:40px;top:120px;width:60px;height:40px;opacity:.9"></div>
  <div class="orange" style="left:300px;top:120px;width:60px;height:40px;opacity:.9"></div>
  <div class="ft"><b>Bright Towns Forum</b><span>Sample footer · Page 9</span></div>
</section>

<section class="slide">
  <h2 class="hd">Timeline 1 Year</h2>
  <svg style="left:10px;top:28px" width="364" height="160" viewBox="0 0 364 160">
    <g fill="#999" font-size="5" font-family="Open Sans, sans-serif">
      <text x="60" y="6">Jan</text><text x="85" y="6">Feb</text><text x="110" y="6">Mar</text><text x="135" y="6">Apr</text><text x="160" y="6">May</text><text x="185" y="6">Jun</text><text x="210" y="6">Jul</text><text x="235" y="6">Aug</text><text x="260" y="6">Sep</text><text x="285" y="6">Oct</text><text x="310" y="6">Nov</text><text x="335" y="6">Dec</text>
    </g>
    <g stroke="#e3e6ea"><line x1="55" y1="12" x2="55" y2="150"/><line x1="130" y1="12" x2="130" y2="150"/><line x1="205" y1="12" x2="205" y2="150"/><line x1="280" y1="12" x2="280" y2="150"/></g>
    <g font-size="5" fill="#555" font-family="Open Sans, sans-serif">
      <text x="0" y="22">Phase 1</text><text x="0" y="37">Phase 2</text><text x="0" y="52">Phase 3</text><text x="0" y="67">Phase 4</text><text x="0" y="82">Phase 5</text><text x="0" y="97">Phase 6</text><text x="0" y="112">Phase 7</text>
    </g>
    <rect x="70" y="17" width="70" height="6" rx="3" fill="#1a9bc2"/>
    <rect x="90" y="32" width="90" height="6" rx="3" fill="#173a6b"/>
    <rect x="130" y="47" width="60" height="6" rx="3" fill="#e8502a"/>
    <rect x="170" y="62" width="80" height="6" rx="3" fill="#7b3f98"/>
    <rect x="95" y="77" width="50" height="6" rx="3" fill="#f29a1f"/>
    <rect x="210" y="92" width="90" height="6" rx="3" fill="#6aa43b"/>
    <rect x="260" y="107" width="70" height="6" rx="3" fill="#173a6b"/>
    <g font-size="4.5" fill="#555" font-family="Open Sans, sans-serif"><rect x="60" y="134" width="8" height="4" fill="#1a9bc2"/><text x="71" y="138">Task</text><rect x="110" y="134" width="8" height="4" fill="#e8502a"/><text x="121" y="138">Task</text><rect x="160" y="134" width="8" height="4" fill="#6aa43b"/><text x="171" y="138">Task</text><rect x="210" y="134" width="8" height="4" fill="#7b3f98"/><text x="221" y="138">Task</text></g>
  </svg>
  <div class="ft"><b>Bright Towns Forum</b><span>Sample footer · Page 10</span></div>
</section>

<section class="slide">
  <h2 class="hd">Timeline 6 month</h2>
  <svg style="left:10px;top:26px" width="364" height="165" viewBox="0 0 364 165">
    <rect x="30" y="0" width="55" height="9" fill="#173a6b"/><rect x="85" y="0" width="55" height="9" fill="#e8502a"/><rect x="140" y="0" width="55" height="9" fill="#7b3f98"/><rect x="195" y="0" width="55" height="9" fill="#f29a1f"/><rect x="250" y="0" width="55" height="9" fill="#6aa43b"/><rect x="305" y="0" width="55" height="9" fill="#1a9bc2"/>
    <g fill="#eceef1"><rect x="0" y="16" width="360" height="10"/><rect x="0" y="38" width="360" height="10"/><rect x="0" y="60" width="360" height="10"/><rect x="0" y="82" width="360" height="10"/><rect x="0" y="104" width="360" height="10"/><rect x="0" y="126" width="360" height="10"/></g>
    <polygon points="40,18 120,18 125,21 120,24 40,24" fill="#173a6b"/>
    <polygon points="100,40 190,40 195,43 190,46 100,46" fill="#e8502a"/>
    <polygon points="150,51 220,51 225,54 220,57 150,57" fill="#e8502a"/>
    <polygon points="80,62 160,62 165,65 160,68 80,68" fill="#173a6b"/>
    <polygon points="200,84 280,84 285,87 280,90 200,90" fill="#f29a1f"/>
    <polygon points="260,106 340,106 345,109 340,112 260,112" fill="#e8502a"/>
    <polygon points="300,128 355,128 360,131 355,134 300,134" fill="#173a6b"/>
    <g fill="#173a6b"><circle cx="70" cy="152" r="2.5"/><circle cx="130" cy="152" r="2.5"/><circle cx="190" cy="152" r="2.5"/><circle cx="250" cy="152" r="2.5"/></g>
  </svg>
  <div class="ft"><b>Bright Towns Forum</b><span>Sample footer · Page 11</span></div>
</section>

<section class="slide">
  <h2 class="hd">Linear Process 4 Steps</h2>
  <svg style="left:20px;top:50px" width="344" height="110" viewBox="0 0 344 110">
    <rect x="20" y="26" width="300" height="8" fill="#173a6b"/>
    <rect x="120" y="26" width="100" height="8" fill="#f29a1f"/>
    <polygon points="320,22 334,30 320,38" fill="#173a6b"/>
    <circle cx="30" cy="30" r="11" fill="#173a6b"/><circle cx="110" cy="70" r="11" fill="#e8502a"/><circle cx="190" cy="30" r="11" fill="#173a6b"/><circle cx="270" cy="70" r="11" fill="#f29a1f"/>
    <path d="M25 30l4 4 7-8" stroke="#fff" stroke-width="2" fill="none"/>
    <g font-size="5" fill="#444" font-family="Open Sans, sans-serif"><text x="90" y="14">Step Two</text><text x="210" y="14">Step Four</text><text x="50" y="66">Step One</text><text x="210" y="66">Step Three</text></g>
  </svg>
  <div class="ft"><b>Bright Towns Forum</b><span>Sample footer · Page 12</span></div>
</section>

<section class="slide">
  <svg style="left:10px;top:40px" width="364" height="120" viewBox="0 0 364 120">
    <rect x="0" y="50" width="70" height="10" fill="#e8502a"/><rect x="72" y="50" width="70" height="10" fill="#173a6b"/><rect x="144" y="50" width="70" height="10" fill="#6aa43b"/><rect x="216" y="50" width="70" height="10" fill="#173a6b"/><rect x="288" y="50" width="70" height="10" fill="#e8502a"/>
    <g font-family="Open Sans, sans-serif" font-weight="700" font-size="14"><text x="15" y="82" fill="#e8502a">01</text><text x="90" y="40" fill="#173a6b">02</text><text x="160" y="82" fill="#f29a1f">03</text><text x="235" y="40" fill="#6aa43b">04</text><text x="310" y="82" fill="#173a6b">05</text><text x="330" y="40" fill="#e8502a">04</text></g>
    <g font-size="4.5" fill="#777" font-family="Open Sans, sans-serif"><text x="10" y="30">Short step note</text><text x="160" y="30">Short step note</text><text x="90" y="80">Short step note</text><text x="235" y="80">Short step note</text></g>
  </svg>
  <div class="ft"><b>Bright Towns Forum</b><span>Sample footer · Page 13</span></div>
</section>

<section class="slide">
  <h2 class="hd">India Map</h2>
  <div style="left:130px;top:30px;width:110px;height:150px;background:linear-gradient(180deg,#bfc4cc,#9aa1ab);border-radius:30% 40% 50% 40%" role="img" aria-label="Map of India with highlighted states"></div>
  <div class="navy" style="left:170px;top:100px;width:30px;height:25px"></div>
  <div class="navy" style="left:260px;top:60px;width:80px;height:22px"></div>
  <div class="orange" style="left:40px;top:110px;width:80px;height:22px"></div>
  <p class="tiny wt" style="left:266px;top:64px">Region One</p>
  <p class="tiny wt" style="left:46px;top:114px">Region Two</p>
  <div class="ft"><b>Bright Towns Forum</b><span>Sample footer · Page 14</span></div>
</section>

<section class="slide">
  <h2 class="hd">North America Map</h2>
  <div style="left:14px;top:40px;font-size:14px;font-weight:700;color:var(--red)">89%</div>
  <div class="navy bar" style="left:14px;top:80px;width:90px;height:6px"></div>
  <div class="orange bar" style="left:14px;top:94px;width:70px;height:6px"></div>
  <div class="bar" style="left:14px;top:108px;width:60px;height:6px;background:var(--red)"></div>
  <div class="navy bar" style="left:14px;top:122px;width:80px;height:6px"></div>
  <div class="bar" style="left:14px;top:136px;width:50px;height:6px;background:var(--green)"></div>
  <div style="left:210px;top:30px;width:150px;height:155px;background:linear-gradient(160deg,#d2d6dc,#a9b0b9);border-radius:40% 30% 45% 20%" role="img" aria-label="Map of North America"></div>
  <div class="orange dot" style="left:250px;top:60px;width:26px;height:26px"></div>
  <div class="dot" style="left:280px;top:120px;width:26px;height:26px;background:var(--red)"></div>
  <div class="ft"><b>Bright Towns Forum</b><span>Sample footer · Page 15</span></div>
</section>

<section class="slide">
  <h2 class="hd">Australia &amp; New Zealand Map</h2>
  <div style="left:14px;top:30px;width:140px;height:110px;background:linear-gradient(135deg,#c5cad1,#a7aeb8);border-radius:35% 45% 40% 50%" role="img" aria-label="Map of Australia and New Zealand"></div>
  <div class="orange" style="left:70px;top:75px;width:30px;height:25px"></div>
  <svg style="left:195px;top:40px" width="70" height="70" viewBox="0 0 70 70">
    <circle cx="35" cy="35" r="28" fill="none" stroke="#e3e6ea" stroke-width="8"/>
    <circle cx="35" cy="35" r="28" fill="none" stroke="#f29a1f" stroke-width="8" stroke-dasharray="120 176" transform="rotate(-90 35 35)"/>
    <circle cx="35" cy="35" r="28" fill="none" stroke="#173a6b" stroke-width="8" stroke-dasharray="30 176" stroke-dashoffset="-120" transform="rotate(-90 35 35)"/>
    <text x="35" y="38" text-anchor="middle" font-size="9" font-weight="700" fill="#173a6b" font-family="Open Sans, sans-serif">12,300</text>
  </svg>
  <p class="tiny" style="left:280px;top:60px;width:90px;color:var(--orange)">Lorem ipsum dolor sit amet elit.</p>
  <div class="ft"><b>Bright Towns Forum</b><span>Sample footer · Page 16</span></div>
</section>

<section class="slide">
  <h2 class="hd">6 Doughnut Chart</h2>
  <svg style="left:14px;top:30px" width="360" height="140" viewBox="0 0 360 140">
    <g fill="none" stroke-width="4">
      <circle cx="20" cy="25" r="14" stroke="#e3e6ea"/><circle cx="20" cy="25" r="14" stroke="#173a6b" stroke-dasharray="66 88" transform="rotate(-90 20 25)"/>
      <circle cx="140" cy="25" r="14" stroke="#e3e6ea"/><circle cx="140" cy="25" r="14" stroke="#1a9bc2" stroke-dasharray="81 88" transform="rotate(-90 140 25)"/>
      <circle cx="260" cy="25" r="14" stroke="#e3e6ea"/><circle cx="260" cy="25" r="14" stroke="#6aa43b" stroke-dasharray="29 88" transform="rotate(-90 260 25)"/>
      <circle cx="20" cy="80" r="14" stroke="#e3e6ea"/><circle cx="20" cy="80" r="14" stroke="#e8502a" stroke-dasharray="44 88" transform="rotate(-90 20 80)"/>
      <circle cx="140" cy="80" r="14" stroke="#e3e6ea"/><circle cx="140" cy="80" r="14" stroke="#f29a1f" stroke-dasharray="54 88" transform="rotate(-90 140 80)"/>
      <circle cx="260" cy="80" r="14" stroke="#e3e6ea"/><circle cx="260" cy="80" r="14" stroke="#7b3f98" stroke-dasharray="29 88" transform="rotate(-90 260 80)"/>
    </g>
    <g font-size="6" font-weight="700" text-anchor="middle" font-family="Open Sans, sans-serif"><text x="20" y="27" fill="#173a6b">75%</text><text x="140" y="27" fill="#1a9bc2">92%</text><text x="260" y="27" fill="#6aa43b">33%</text><text x="20" y="82" fill="#e8502a">50%</text><text x="140" y="82" fill="#f29a1f">61%</text><text x="260" y="82" fill="#7b3f98">33%</text></g>
    <g font-size="5" font-family="Open Sans, sans-serif" font-weight="700"><text x="40" y="22" fill="#173a6b">Graphic Design</text><text x="160" y="22" fill="#1a9bc2">SEO Analysis</text><text x="280" y="22" fill="#6aa43b">Marketing</text><text x="40" y="77" fill="#e8502a">Web Design</text><text x="160" y="77" fill="#f29a1f">Marketing</text><text x="280" y="77" fill="#7b3f98">Video Editing</text></g>
    <g font-size="4" fill="#888" font-family="Open Sans, sans-serif"><text x="40" y="30">Short caption</text><text x="160" y="30">Short caption</text><text x="280" y="30">Short caption</text><text x="40" y="85">Short caption</text><text x="160" y="85">Short caption</text><text x="280" y="85">Short caption</text></g>
  </svg>
  <div class="ft"><b>Bright Towns Forum</b><span>Sample footer · Page 17</span></div>
</section>

<section class="slide">
  <h2 class="hd">Full Page Bar Chart</h2>
  <svg style="left:14px;top:28px" width="360" height="160" viewBox="0 0 360 160">
    <g stroke="#eceef1"><line x1="10" y1="30" x2="355" y2="30"/><line x1="10" y1="70" x2="355" y2="70"/><line x1="10" y1="110" x2="355" y2="110"/><line x1="10" y1="150" x2="355" y2="150"/></g>
    <g>
      <rect x="30" y="125" width="7" height="25" fill="#173a6b"/><rect x="38" y="130" width="7" height="20" fill="#e8502a"/>
      <rect x="60" y="120" width="7" height="30" fill="#173a6b"/><rect x="68" y="126" width="7" height="24" fill="#f29a1f"/>
      <rect x="90" y="115" width="7" height="35" fill="#173a6b"/><rect x="98" y="120" width="7" height="30" fill="#e8502a"/>
      <rect x="120" y="118" width="7" height="32" fill="#173a6b"/><rect x="128" y="112" width="7" height="38" fill="#f29a1f"/>
      <rect x="150" y="110" width="7" height="40" fill="#173a6b"/><rect x="158" y="115" width="7" height="35" fill="#e8502a"/>
      <rect x="180" y="105" width="7" height="45" fill="#173a6b"/><rect x="188" y="100" width="7" height="50" fill="#f29a1f"/>
      <rect x="210" y="100" width="7" height="50" fill="#173a6b"/><rect x="218" y="95" width="7" height="55" fill="#e8502a"/>
      <rect x="240" y="90" width="7" height="60" fill="#173a6b"/><rect x="248" y="95" width="7" height="55" fill="#f29a1f"/>
      <rect x="270" y="80" width="7" height="70" fill="#173a6b"/><rect x="278" y="75" width="7" height="75" fill="#e8502a"/>
      <rect x="300" y="70" width="7" height="80" fill="#173a6b"/><rect x="308" y="60" width="7" height="90" fill="#f29a1f"/>
      <rect x="330" y="25" width="9" height="125" fill="#7b3f98"/>
    </g>
    <rect x="300" y="8" width="45" height="10" fill="#7b3f98"/>
    <text x="322" y="15" font-size="5" fill="#fff" text-anchor="middle" font-family="Open Sans, sans-serif">20% growth</text>
  </svg>
  <div class="ft"><b>Bright Towns Forum</b><span>Sample footer · Page 18</span></div>
</section>

<section class="slide">
  <div class="ph ph-dusk" style="left:0;top:0;right:0;height:100px" role="img" aria-label="Skyline at dusk"></div>
  <div class="navy" style="left:0;top:0;width:128px;height:100px;opacity:.85"></div>
  <h2 class="big-title wt" style="left:12px;top:28px;font-size:13px">Your Global<br>Lead Partner</h2>
  <div class="navy" style="left:0;top:100px;width:128px;bottom:0"></div>
  <div class="orange" style="left:128px;top:100px;width:128px;bottom:0"></div>
  <div style="left:256px;top:100px;width:128px;bottom:0;background:var(--green)"></div>
  <div class="dot" style="left:52px;top:112px;width:22px;height:22px;border:2px solid #fff"></div>
  <div class="dot" style="left:180px;top:112px;width:22px;height:22px;border:2px solid #fff"></div>
  <div class="dot" style="left:308px;top:112px;width:22px;height:22px;border:2px solid #fff"></div>
  <p class="tiny wt" style="left:14px;top:145px;width:100px;text-align:center">Lorem ipsum dolor sit amet consectetur elit.</p>
  <p class="tiny wt" style="left:142px;top:145px;width:100px;text-align:center">Lorem ipsum dolor sit amet consectetur elit.</p>
  <p class="tiny wt" style="left:270px;top:145px;width:100px;text-align:center">Lorem ipsum dolor sit amet consectetur elit.</p>
</section>

<section class="slide">
  <h2 class="hd">Process Slide</h2>
  <svg style="left:30px;top:30px" width="320" height="150" viewBox="0 0 320 150">
    <g stroke="#173a6b" stroke-width="2" fill="none"><polyline points="0,140 60,140 60,110 120,110 120,85 180,85 180,55 240,55 240,30 300,30"/></g>
    <g font-family="Open Sans, sans-serif" font-weight="700" font-size="13" fill="#173a6b"><text x="8" y="135">01</text><text x="68" y="105">02</text><text x="128" y="80">03</text><text x="188" y="50">04</text></g>
    <g font-size="4.5" fill="#666" font-family="Open Sans, sans-serif"><text x="26" y="130">Your Text Here</text><text x="86" y="100">Your Text Here</text><text x="146" y="75">Your Text Here</text><text x="206" y="45">Your Text Here</text></g>
  </svg>
  <div class="ft"><b>Bright Towns Forum</b><span>Sample footer · Page 19</span></div>
</section>

<section class="slide">
  <div class="navy" style="left:0;top:0;width:130px;bottom:0"></div>
  <h2 class="big-title wt" style="left:14px;top:60px;width:105px;font-size:13px">Right Bar Chart Title Here</h2>
  <p class="tiny wt" style="left:14px;top:110px;width:105px">Lorem ipsum dolor sit amet, consectetur adipiscing elit sed do.</p>
  <svg style="left:150px;top:30px" width="220" height="100" viewBox="0 0 220 100">
    <g><rect x="10" y="50" width="10" height="50" fill="#173a6b"/><rect x="22" y="40" width="10" height="60" fill="#f29a1f"/><rect x="50" y="30" width="10" height="70" fill="#173a6b"/><rect x="62" y="45" width="10" height="55" fill="#f29a1f"/><rect x="90" y="55" width="10" height="45" fill="#173a6b"/><rect x="102" y="35" width="10" height="65" fill="#f29a1f"/><rect x="130" y="20" width="10" height="80" fill="#173a6b"/><rect x="142" y="40" width="10" height="60" fill="#f29a1f"/><rect x="170" y="30" width="10" height="70" fill="#173a6b"/><rect x="182" y="10" width="10" height="90" fill="#f29a1f"/></g>
  </svg>
  <div style="left:160px;top:150px;font-size:18px;font-weight:700;color:var(--orange)">85%</div>
  <p class="tiny" style="left:230px;top:152px;width:140px">Lorem ipsum dolor sit amet, consectetur elit.</p>
</section>

<section class="slide">
  <h2 class="hd">Three Column Table</h2>
  <table class="grid" style="left:8px;top:36px;width:118px">
    <tr><th colspan="4">Your Table Title</th></tr>
    <tr><td>A</td><td>1</td><td>2</td><td>3</td></tr><tr><td>B</td><td>4</td><td>5</td><td>6</td></tr><tr><td>C</td><td>7</td><td>8</td><td>9</td></tr><tr><td>D</td><td>1</td><td>2</td><td>3</td></tr><tr><td>E</td><td>4</td><td>5</td><td>6</td></tr>
  </table>
  <table class="grid" style="left:133px;top:36px;width:118px">
    <tr><th colspan="4">Your Table Title</th></tr>
    <tr><td>A</td><td>1</td><td>2</td><td>3</td></tr><tr><td>B</td><td>4</td><td>5</td><td>6</td></tr><tr><td>C</td><td>7</td><td>8</td><td>9</td></tr><tr><td>D</td><td>1</td><td>2</td><td>3</td></tr><tr><td>E</td><td>4</td><td>5</td><td>6</td></tr>
  </table>
  <table class="grid" style="left:258px;top:36px;width:118px">
    <tr><th colspan="4">Your Table Title</th></tr>
    <tr><td>A</td><td>1</td><td>2</td><td>3</td></tr><tr><td>B</td><td>4</td><td>5</td><td>6</td></tr><tr><td>C</td><td>7</td><td>8</td><td>9</td></tr><tr><td>D</td><td>1</td><td>2</td><td>3</td></tr><tr><td>E</td><td>4</td><td>5</td><td>6</td></tr>
  </table>
  <div class="ft"><b>Bright Towns Forum</b><span>Sample footer · Page 20</span></div>
</section>

<section class="slide">
  <h2 class="hd">3 Iterative Process</h2>
  <svg style="left:140px;top:32px" width="110" height="110" viewBox="0 0 110 110">
    <g fill="none" stroke-width="16">
      <circle cx="55" cy="55" r="38" stroke="#e8502a" stroke-dasharray="76 239" transform="rotate(-90 55 55)"/>
      <circle cx="55" cy="55" r="38" stroke="#173a6b" stroke-dasharray="76 239" stroke-dashoffset="-80" transform="rotate(-90 55 55)"/>
      <circle cx="55" cy="55" r="38" stroke="#f29a1f" stroke-dasharray="76 239" stroke-dashoffset="-160" transform="rotate(-90 55 55)"/>
    </g>
  </svg>
  <p class="h-sm" style="left:40px;top:50px;font-size:6px;color:var(--navy)">New Management</p>
  <p class="h-sm" style="left:270px;top:40px;font-size:6px;color:var(--red)">Target Expansion</p>
  <p class="h-sm" style="left:235px;top:120px;font-size:6px;color:var(--navy)">System Solution</p>
  <p class="tiny" style="left:40px;top:60px;width:90px">Short supporting text here.</p>
  <p class="tiny" style="left:270px;top:50px;width:90px">Short supporting text here.</p>
  <div class="ft"><b>Bright Towns Forum</b><span>Sample footer · Page 21</span></div>
</section>

<section class="slide">
  <h2 class="hd">4 Iterative Process</h2>
  <svg style="left:140px;top:32px" width="110" height="110" viewBox="0 0 110 110">
    <g fill="none" stroke-width="16">
      <circle cx="55" cy="55" r="38" stroke="#173a6b" stroke-dasharray="56 239" transform="rotate(-90 55 55)"/>
      <circle cx="55" cy="55" r="38" stroke="#f29a1f" stroke-dasharray="56 239" stroke-dashoffset="-60" transform="rotate(-90 55 55)"/>
      <circle cx="55" cy="55" r="38" stroke="#e8502a" stroke-dasharray="56 239" stroke-dashoffset="-120" transform="rotate(-90 55 55)"/>
      <circle cx="55" cy="55" r="38" stroke="#1a9bc2" stroke-dasharray="56 239" stroke-dashoffset="-180" transform="rotate(-90 55 55)"/>
    </g>
  </svg>
  <p class="h-sm" style="left:50px;top:36px;font-size:6px;color:var(--navy)">Strong Management</p>
  <p class="h-sm" style="left:290px;top:40px;font-size:6px;color:var(--navy)">System Upscaling</p>
  <p class="h-sm" style="left:60px;top:120px;font-size:6px;color:var(--red)">Budget</p>
  <p class="h-sm" style="left:290px;top:125px;font-size:6px;color:var(--orange)">Time Management</p>
  <div class="ft"><b>Bright Towns Forum</b><span>Sample footer · Page 22</span></div>
</section>

<section class="slide">
  <h2 class="hd">6 Iterative Process</h2>
  <svg style="left:130px;top:28px" width="130" height="130" viewBox="0 0 130 130">
    <g fill="none" stroke-width="18">
      <circle cx="65" cy="65" r="44" stroke="#7b3f98" stroke-dasharray="42 277" transform="rotate(-90 65 65)"/>
      <circle cx="65" cy="65" r="44" stroke="#1a9bc2" stroke-dasharray="42 277" stroke-dashoffset="-46" transform="rotate(-90 65 65)"/>
      <circle cx="65" cy="65" r="44" stroke="#6aa43b" stroke-dasharray="42 277" stroke-dashoffset="-92" transform="rotate(-90 65 65)"/>
      <circle cx="65" cy="65" r="44" stroke="#f29a1f" stroke-dasharray="42 277" stroke-dashoffset="-138" transform="rotate(-90 65 65)"/>
      <circle cx="65" cy="65" r="44" stroke="#e8502a" stroke-dasharray="42 277" stroke-dashoffset="-184" transform="rotate(-90 65 65)"/>
      <circle cx="65" cy="65" r="44" stroke="#173a6b" stroke-dasharray="42 277" stroke-dashoffset="-230" transform="rotate(-90 65 65)"/>
    </g>
  </svg>
  <p class="h-sm" style="left:60px;top:42px;font-size:6px;color:var(--navy)">Content 1</p>
  <p class="h-sm" style="left:40px;top:90px;font-size:6px;color:var(--red)">Content 2</p>
  <p class="h-sm" style="left:60px;top:135px;font-size:6px;color:var(--navy)">Content 6</p>
  <p class="h-sm" style="left:280px;top:32px;font-size:6px;color:var(--purple)">Content 3</p>
  <p class="h-sm" style="left:290px;top:80px;font-size:6px;color:var(--teal)">Content 4</p>
  <p class="h-sm" style="left:280px;top:130px;font-size:6px;color:var(--green)">Content 5</p>
  <div class="ft"><b>Bright Towns Forum</b><span>Sample footer · Page 23</span></div>
</section>

<section class="slide">
  <p class="tiny" style="left:12px;top:10px;width:160px">Lorem ipsum dolor sit amet, consectetur adipiscing elit, sed do eiusmod tempor incididunt ut labore et dolore magna aliqua ut enim.</p>
  <div class="ph ph-day" style="left:195px;top:0;right:0;height:75px" role="img" aria-label="City skyline by day"></div>
  <div class="ph ph-dusk" style="left:0;top:75px;width:190px;bottom:0" role="img" aria-label="Skyline at dusk"></div>
  <div class="navy" style="left:190px;top:75px;right:0;height:70px"></div>
  <p class="tiny wt" style="left:200px;top:85px;width:170px">Lorem ipsum dolor sit amet, consectetur adipiscing elit, sed do eiusmod tempor incididunt ut labore.</p>
  <div class="orange" style="left:190px;top:145px;width:100px;bottom:0"></div>
  <div class="ph ph-aerial" style="left:290px;top:145px;right:0;bottom:0" role="img" aria-label="Aerial view of buildings"></div>
</section>

<section class="slide">
  <h2 class="hd">Three Picture With Description</h2>
  <div class="ph ph-aerial" style="left:10px;top:28px;width:120px;height:75px" role="img" aria-label="Aerial view of a plaza"></div>
  <div class="orange" style="left:130px;top:28px;width:120px;height:75px"></div>
  <div class="ph ph-night" style="left:250px;top:28px;width:124px;height:75px" role="img" aria-label="City lights at night"></div>
  <div class="navy" style="left:10px;top:103px;width:120px;height:75px"></div>
  <div class="ph ph-dusk" style="left:130px;top:103px;width:120px;height:75px" role="img" aria-label="Skyline at dusk"></div>
  <div class="navy" style="left:250px;top:103px;width:124px;height:75px"></div>
  <p class="h-sm wt" style="left:138px;top:36px;font-size:6px">Heading Goes Here</p>
  <p class="h-sm wt" style="left:18px;top:111px;font-size:6px">Heading Goes Here</p>
  <p class="h-sm wt" style="left:258px;top:111px;font-size:6px">Heading Goes Here</p>
  <div class="ft"><b>Bright Towns Forum</b><span>Sample footer · Page 24</span></div>
</section>

<section class="slide">
  <div class="ph ph-night" style="inset:0" role="img" aria-label="Aerial view of a dense city"></div>
  <div class="navy" style="left:30px;top:0;width:110px;height:150px;opacity:.85"></div>
  <h2 class="big-title wt" style="left:42px;top:60px;width:95px;font-size:13px;font-weight:400">This Is Your Topic Cluster Page</h2>
</section>

<section class="slide navy">
  <h2 class="big-title wt" style="left:0;right:0;top:78px;text-align:center;font-size:13px;font-weight:400">This Is Your Topic Cluster Page</h2>
  <div class="logo inv" style="left:0;right:0;top:112px;text-align:center;font-size:11px">Bright Towns Forum</div>
</section>

<section class="slide" style="background:var(--red)">
  <h2 class="big-title wt" style="left:0;right:0;top:85px;text-align:center;font-size:13px;font-weight:400">This Is Your Topic<br>Cluster Page</h2>
</section>

<section class="slide last orange">
  <h2 class="big-title wt" style="left:0;right:0;top:85px;text-align:center;font-size:13px;font-weight:400">This Is Your Topic<br>Cluster Page</h2>
</section>

</main>
</body>
</html>
```